Business Card Design for company

We want new business cards. We'd like something different-- yet still highly professional. Our tagline is Providing leadership, delivering success. Stock photos are ok, as long as they are relevant and look upscale.

Target Market(s)

Architecture/Business Management Consulting/Engineering Consulting

Contact Information for Business Card

dark gray background with pops of blue might be good, but you tell me. You're the designers. Rounded corners might be nice, but again, you tell me.

Font styles to use
Serif
Sans Serif

Colors
3276b5
5c5c5c
9d9d9d
fbfbfb

Requirements
Nice to have
• Something different, but still very professional.

```html
<!DOCTYPE html>
<html lang="en">
<head>
<meta charset="utf-8">
<title>Norvale Partners – Business Card</title>
<link rel="stylesheet" href="https://fonts.googleapis.com/css2?family=Oswald:wght@500&family=Work+Sans:wght@400;500&family=Montserrat:wght@600&display=swap">
<style>
  :root {
    --blue: #3276b5;
    --blue-deep: #1f5a93;
    --grey-dark: #5c5c5c;
    --grey-mid: #9d9d9d;
    --paper: #fbfbfb;
    --card-dark: #262627;
    --backdrop: #d9d9db;
  }
  * { margin: 0; padding: 0; box-sizing: border-box; }
  html, body { width: 1200px; height: 900px; overflow: hidden; }
  body {
    background: var(--backdrop);
    display: flex;
    flex-direction: column;
    align-items: center;
    justify-content: center;
    gap: 56px;
    font-family: "Work Sans", sans-serif;
  }
  .card {
    width: 600px;
    height: 343px;
    position: relative;
    box-shadow: 0 10px 28px rgba(0,0,0,.22);
    overflow: hidden;
  }

  /* front */
  .card-front {
    background: radial-gradient(ellipse at 70% 65%, #ffffff 0%, var(--paper) 45%, #e9eaec 100%);
  }
  .identity {
    position: absolute;
    left: 60px;
    top: 92px;
    width: 250px;
    text-align: right;
  }
  .person-name {
    font-family: "Oswald", sans-serif;
    font-weight: 500;
    font-size: 36px;
    letter-spacing: 0.5px;
    color: var(--blue-deep);
    text-transform: uppercase;
    line-height: 1.1;
  }
  .person-role {
    font-size: 14px;
    color: var(--grey-dark);
    margin-top: 4px;
  }
  .divider {
    position: absolute;
    left: 330px;
    top: 122px;
    width: 2px;
    height: 64px;
    background: var(--blue-deep);
  }
  .contact-list {
    position: absolute;
    left: 348px;
    top: 120px;
    list-style: none;
    font-size: 14px;
    color: var(--grey-dark);
  }
  .contact-list li {
    display: flex;
    align-items: center;
    gap: 8px;
    height: 22px;
  }
  .contact-list svg { width: 11px; height: 11px; fill: var(--blue); }
  .contact-list .web-accent { color: var(--blue-deep); }
  .address {
    position: absolute;
    left: 60px;
    bottom: 48px;
    font-size: 14px;
    color: var(--grey-dark);
    letter-spacing: 0.3px;
  }

  /* back */
  .card-back {
    background: var(--card-dark);
    display: flex;
    flex-direction: column;
    align-items: center;
    justify-content: center;
  }
  .brand-name {
    font-family: "Work Sans", sans-serif;
    font-weight: 500;
    font-size: 40px;
    letter-spacing: 5px;
    color: #d7d8da;
    text-transform: uppercase;
    display: flex;
    align-items: center;
    gap: 16px;
  }
  .brand-mark {
    width: 18px;
    height: 18px;
    background: var(--blue);
  }
  .web-rule {
    display: flex;
    align-items: center;
    gap: 14px;
    margin-top: 34px;
    font-size: 13px;
    color: #c9c9cb;
    letter-spacing: 0.4px;
  }
  .web-rule::before, .web-rule::after {
    content: "";
    width: 110px;
    height: 1px;
    background: var(--grey-mid);
  }
</style>
</head>
<body>

  <section class="card card-front" aria-label="Card front">
    <div class="identity">
      <h1 class="person-name">Daniel Harper</h1>
      <p class="person-role">Director</p>
    </div>
    <span class="divider"></span>
    <ul class="contact-list">
      <li>
        <svg viewBox="0 0 24 24" aria-hidden="true"><path d="M6.6 10.8a15 15 0 0 0 6.6 6.6l2.2-2.2a1 1 0 0 1 1-.25 11.4 11.4 0 0 0 3.6.57 1 1 0 0 1 1 1V20a1 1 0 0 1-1 1A17 17 0 0 1 3 4a1 1 0 0 1 1-1h3.5a1 1 0 0 1 1 1c0 1.25.2 2.45.57 3.57a1 1 0 0 1-.25 1z"/></svg>
        (514) 555-0142
      </li>
      <li>
        <svg viewBox="0 0 24 24" aria-hidden="true"><path d="M2 5h20v14H2zm2 2v.5l8 5 8-5V7zm0 2.9V17h16V9.9l-8 5z"/></svg>
        info@norvalepartners.com
      </li>
      <li>
        <svg viewBox="0 0 24 24" aria-hidden="true"><circle cx="12" cy="12" r="10"/></svg>
        <span>www.<span class="web-accent">norvalepartners</span>.com</span>
      </li>
    </ul>
    <p class="address">212b Harlow Street, Riverton, NZ, 8042</p>
  </section>

  <section class="card card-back" aria-label="Card back">
    <p class="brand-name"><span class="brand-mark"></span>Norvale Partners</p>
    <p class="web-rule">www.norvalepartners.com</p>
  </section>

</body>
</html>
```